Wealth Education Business Needs Sharp Business Card Design

We need a business card design for a recently launched investor education business called Harbor Crest.

The final design should promote security, empowerment, self improvement and financial gain. The card will ideally promote the stature of the business.

For more information and colours please visit harborcrest.com.au

Target Market(s)

Corporate executives and high net worth individuals

Industry/Entity Type

Education

Contact Information for Business Card

```html
<!DOCTYPE html>
<html lang="en">
<head>
<meta charset="utf-8">
<title>Harbor Crest – Business Card</title>
<link rel="stylesheet" href="https://fonts.googleapis.com/css2?family=Lato:wght@400;700&display=swap">
<style>
  :root {
    --navy: #1f2a3c;
    --ink: #2f3338;
    --muted: #4a4d52;
    --paper: #fbfbfb;
    --band-grey: #5b5e63;
    --stage: #e4e2df;
    --white: #ffffff;
  }
  * { margin: 0; padding: 0; box-sizing: border-box; }
  html, body {
    width: 1200px;
    height: 960px;
    overflow: hidden;
  }
  body {
    position: relative;
    background: var(--stage);
    font-family: "Lato", sans-serif;
  }
  .card {
    position: absolute;
    left: 270px;
    width: 645px;
    height: 368px;
    box-shadow: 0 6px 18px rgba(0,0,0,0.18);
    overflow: hidden;
  }

  /* Front */
  .card-front { top: 83px; background: var(--navy); }
  .card-front .brand-name {
    position: absolute;
    left: 0; right: 0;
    top: 160px;
    text-align: center;
    color: var(--white);
    font-size: 40px;
    font-weight: 400;
    letter-spacing: 0.2em;
    text-transform: uppercase;
  }
  .card-front .site {
    position: absolute;
    left: 0; right: 0;
    top: 315px;
    text-align: center;
    color: var(--white);
    font-size: 14px;
  }

  /* Back */
  .card-back { top: 507px; background: var(--paper); }
  .holder { position: absolute; left: 63px; top: 61px; }
  .holder-name { font-size: 19px; font-weight: 700; color: var(--navy); line-height: 24px; }
  .holder-role { font-size: 15px; color: var(--muted); line-height: 20px; }
  .card-back .brand-name {
    position: absolute;
    right: 42px;
    top: 64px;
    color: var(--ink);
    font-size: 30px;
    font-weight: 400;
    letter-spacing: 0.2em;
    text-transform: uppercase;
  }
  .address {
    position: absolute;
    left: 63px; top: 151px;
    font-size: 15px; line-height: 19px;
    color: var(--muted);
    font-style: normal;
  }
  .contacts {
    position: absolute;
    left: 63px; top: 223px;
    list-style: none;
    font-size: 15px;
    color: var(--muted);
  }
  .contacts li {
    display: flex;
    align-items: center;
    height: 20.7px;
  }
  .contacts svg { width: 16px; height: 16px; margin-right: 13px; fill: var(--ink); }
  .brand-pattern {
    position: absolute;
    left: 368px; top: 130px;
    width: 277px; height: 221px;
    background: linear-gradient(90deg, rgba(186,215,232,0.35), rgba(200,210,215,0.45) 50%, rgba(214,226,190,0.4));
    -webkit-mask-image: linear-gradient(to top, #000 40%, transparent);
            mask-image: linear-gradient(to top, #000 40%, transparent);
  }
  .bands { position: absolute; left: 0; top: 0; width: 645px; height: 368px; }
</style>
</head>
<body>

<section class="card card-front" aria-label="Card front">
  <div class="brand-name">Harbor Crest</div>
  <div class="site">www.harborcrest.com.au</div>
</section>

<section class="card card-back" aria-label="Card back">
  <div class="brand-pattern" role="img" aria-label="Faint decorative brand pattern"></div>
  <svg class="bands" viewBox="0 0 645 368" aria-hidden="true">
    <polygon points="0,338 308,338 336,368 0,368" fill="#1f2a3c"/>
    <polygon points="326,351 645,351 645,368 342,368" fill="#5b5e63"/>
  </svg>

  <div class="holder">
    <div class="holder-name">Daniel Mercer</div>
    <div class="holder-role">Founder &amp; CEO</div>
  </div>

  <div class="brand-name">Harbor Crest</div>

  <address class="address">
    Level 2, 76 Ashgrove Lane<br>
    Melbourne VIC 3000
  </address>

  <ul class="contacts">
    <li>
      <svg viewBox="0 0 16 16"><path d="M2 5c0-2 2-3 6-3s6 1 6 3v1h-3V5H5v1H2z M4 7h8l2 6H2z"/></svg>
      1300.555.018
    </li>
    <li>
      <svg viewBox="0 0 16 16"><path d="M4 0h8a1 1 0 0 1 1 1v14a1 1 0 0 1-1 1H4a1 1 0 0 1-1-1V1a1 1 0 0 1 1-1zm1 2v10h6V2zm3 11a1 1 0 1 0 0 2 1 1 0 0 0 0-2z"/></svg>
      0000.000.000
    </li>
    <li>
      <svg viewBox="0 0 16 16"><path d="M1 3h14v10H1z M2 4.2v.3l6 4.2 6-4.2v-.3z" fill-rule="evenodd"/></svg>
      support@harborcrest.com.au
    </li>
    <li>
      <svg viewBox="0 0 16 16"><path d="M8 1a7 7 0 1 0 0 14A7 7 0 0 0 8 1zm0 1.5c.8.8 1.4 2.1 1.6 3.7H6.4C6.6 4.6 7.2 3.3 8 2.5zM2.6 7.2h2.8c0 .6 0 1.1.1 1.6H2.6a5.5 5.5 0 0 1 0-1.6zm3.8 0h3.2v1.6H6.4zm4.2 0h2.8a5.5 5.5 0 0 1 0 1.6h-2.8zM8 13.5c-.8-.8-1.4-2.1-1.6-3.7h3.2c-.2 1.6-.8 2.9-1.6 3.7z"/></svg>
      www.harborcrest.com.au
    </li>
  </ul>
</section>

</body>
</html>
```